Web Developer Needs a Business Card Design

I need a personal business card design that represents me as a web developer for potential employers. I would like the background to be a dark color on the front for contrast with my logo and name. The back will have all my information along with a smaller version of the logo. I want something with a modern look and feel, not too conservative. This will be used for potential employers and freelance work.

Industry/Entity Type

Business

Contact Information for Business Card

Front should have my logo and name. The back should have all my personal information which would include: name: Tom Varulek, phone: 570-614-3098, email: tomvarulek@quillbox.net, website url: www.tomvarulek.net, logo, web developer.

Font styles to use
Sans Serif

Requirements
Must have
• Must include my logo. The color palette base color will be the logo color.

```html
<!DOCTYPE html>
<html lang="en">
<head>
<meta charset="utf-8">
<title>Tom Varulek – Business Card</title>
<link href="https://fonts.googleapis.com/css2?family=Roboto:wght@400;500;700&display=swap" rel="stylesheet">
<style>
  :root {
    --backdrop: #a7a4a5;
    --card-dark: #0b0b0b;
    --card-dark-soft: #161616;
    --teal: #56e0c2;
    --ink: #111111;
    --white: #ffffff;
  }
  * { margin: 0; padding: 0; box-sizing: border-box; }
  html, body { width: 1200px; height: 1200px; overflow: hidden; }
  body {
    background: var(--backdrop);
    font-family: "Roboto", Arial, sans-serif;
    position: relative;
  }
  .card {
    position: absolute;
    left: 244px;
    width: 712px;
    height: 420px;
    border-radius: 24px;
    overflow: hidden;
    background: var(--card-dark);
  }
  .card--front { top: 118px; }
  .card--back { top: 644px; }
  .card__photo {
    position: absolute; inset: 0;
    background: linear-gradient(135deg, var(--card-dark-soft) 0%, var(--card-dark) 55%, var(--card-dark-soft) 100%);
  }
  .brand {
    position: absolute;
    display: flex;
    align-items: center;
    gap: 18px;
    color: var(--teal);
    font-weight: 700;
  }
  .brand__ring {
    border: 8px solid var(--teal);
    border-radius: 50%;
    flex: none;
  }
  .card--front .brand {
    left: 0; right: 0; top: 150px;
    justify-content: center;
    font-size: 40px;
  }
  .card--front .brand__ring { width: 110px; height: 110px; }
  .card--back .brand {
    left: 110px; top: 70px;
    font-size: 30px;
  }
  .card--back .brand__ring { width: 120px; height: 120px; border-width: 7px; }
  .wave { position: absolute; inset: 0; }
  .identity {
    position: absolute;
    left: 80px; top: 256px;
    width: 220px;
    text-align: center;
  }
  .identity__name { color: var(--teal); font-size: 27px; font-weight: 700; }
  .identity__role { color: var(--white); font-size: 16px; margin-top: 4px; }
  .contacts {
    position: absolute;
    right: 18px; top: 304px;
    list-style: none;
  }
  .contacts li {
    display: flex;
    justify-content: flex-end;
    align-items: center;
    gap: 12px;
    height: 28px;
    font-size: 17px;
    color: var(--ink);
  }
  .contacts svg { width: 16px; height: 16px; flex: none; }
</style>
</head>
<body>
  <section class="card card--front">
    <div class="card__photo" role="img" aria-label="Dark desk photo with laptop keyboard and papers"></div>
    <div class="brand"><span class="brand__ring"></span>Tom Varulek</div>
  </section>

  <section class="card card--back">
    <div class="card__photo" role="img" aria-label="Dark desk photo with laptop keyboard and papers"></div>
    <div class="brand"><span class="brand__ring"></span>Tom Varulek</div>
    <svg class="wave" viewBox="0 0 712 420" aria-hidden="true">
      <path d="M0,330 C160,395 340,372 450,286 C545,212 640,178 712,176 L712,420 L0,420 Z" fill="var(--teal)"/>
      <path d="M0,348 C170,420 380,388 520,300 C400,400 190,432 0,382 Z" fill="var(--card-dark)"/>
      <path d="M0,392 C160,430 330,410 430,372 C320,420 150,440 0,410 Z" fill="var(--card-dark)"/>
    </svg>
    <div class="identity">
      <div class="identity__name">Tom Varulek</div>
      <div class="identity__role">Web Developer</div>
    </div>
    <ul class="contacts">
      <li>570-614-3098
        <svg viewBox="0 0 16 16"><path d="M2 6 C2 3 14 3 14 6 L11 7 L10 5 H6 L5 7 Z M4 9 H12 L13 14 H3 Z" fill="var(--ink)"/></svg>
      </li>
      <li>www.tomvarulek.net
        <svg viewBox="0 0 16 16" fill="none" stroke="var(--ink)" stroke-width="1.4"><circle cx="8" cy="8" r="6.5"/><ellipse cx="8" cy="8" rx="3" ry="6.5"/><path d="M1.5 8 H14.5"/></svg>
      </li>
      <li>tomvarulek@quillbox.net
        <svg viewBox="0 0 16 16"><rect x="1" y="3" width="14" height="10" fill="var(--ink)"/><path d="M1.5 3.5 L8 9 L14.5 3.5" fill="none" stroke="var(--teal)" stroke-width="1.2"/></svg>
      </li>
    </ul>
  </section>
</body>
</html>
```